Seeking funky, innovative business cards

I am looking to refresh our current business cards to something more engaging, visual and impactful. We are a management consultancy firm, see website (www.larkstone-partners.com.au). I've included our colour scheme, sample of the slides we use and our old business cards. We would like our cards to have icons. The card should display:- Name- Title- Mobile number- Address- Email address- Website - Company logo- Our purpose statement "We build workplaces people are proud to join"

Contact Information for Business Card

Brennan Ulfsson
Consultant
0468 927 341
Level 3, 218 Wexley Street, Melbourne 3000
brennan@larkstone-partners.com.au
www.larkstone-partners.com.au

Purpose statement "We build workplaces people are proud to join"
LOGO available in google images

Font styles to use
Other font styles liked:
• Open Sans Light, Bebas Neue (open to other cool foints)

Colors
ffc214
5c5c5c
f5f5f5
fefefe

Requirements
Must have
• - Name
• - Title
• - Mobile number
• - Address
• - Email address
• - Website
• - Company logo
• - Our purpose statement "We build workplaces people are proud to join"
Nice to have
• - Icons
• - Colour (see our colour scheme"

```html
<!DOCTYPE html>
<html lang="en">
<head>
<meta charset="utf-8">
<title>Larkstone Partners – Business Card</title>
<link rel="stylesheet" href="https://fonts.googleapis.com/css2?family=Open+Sans:wght@300;400;600;700&display=swap">
<style>
  :root {
    --brand-yellow: #e3ae14;
    --brand-grey: #3f4142;
    --card-white: #f2f2f2;
    --ink-white: #fefefe;
    --backdrop: #3a3a3a;
  }
  * { margin: 0; padding: 0; box-sizing: border-box; }
  html, body {
    width: 1200px;
    height: 829px;
    overflow: hidden;
    background: var(--backdrop);
    font-family: "Open Sans", Arial, sans-serif;
  }
  .stage { position: relative; width: 1200px; height: 829px; }
  .card {
    position: absolute;
    top: 282px;
    width: 485px;
    height: 277px;
    box-shadow: 0 4px 10px rgba(0,0,0,0.35);
  }
  .card--front { left: 82px; background: var(--brand-yellow); }
  .card--back { left: 628px; background: var(--card-white); }
  .card svg { display: block; width: 100%; height: 100%; }
  .wordmark { font-family: "Open Sans", Arial, sans-serif; font-weight: 300; }
  .purpose { font-family: "Open Sans", Arial, sans-serif; font-weight: 700; letter-spacing: 0.2px; }
  .contact { font-family: "Open Sans", Arial, sans-serif; font-weight: 400; }
  .person-name { font-family: "Open Sans", Arial, sans-serif; font-weight: 700; letter-spacing: 0.6px; }
  .person-title { font-family: "Open Sans", Arial, sans-serif; font-weight: 400; }
</style>
</head>
<body>
<main class="stage">

  <section class="card card--front" aria-label="Card front">
    <svg viewBox="0 0 606 346" xmlns="http://www.w3.org/2000/svg">
      <circle cx="302" cy="142" r="7" fill="var(--ink-white)"/>
      <text class="wordmark" x="302" y="222" text-anchor="middle" font-size="62" fill="var(--ink-white)">Larkstone</text>
      <text class="purpose" x="302" y="304" text-anchor="middle" font-size="14" fill="var(--ink-white)">WE BUILD WORKPLACES PEOPLE ARE PROUD TO JOIN</text>
    </svg>
  </section>

  <section class="card card--back" aria-label="Card back">
    <svg viewBox="0 0 606 346" xmlns="http://www.w3.org/2000/svg">
      <circle cx="548" cy="58" r="6" fill="var(--brand-yellow)"/>
      <text class="wordmark" x="558" y="122" text-anchor="end" font-size="54" fill="var(--brand-grey)">Larkstone</text>

      <polygon class="band-yellow" points="0,170 293,170 353,313 0,313" fill="var(--brand-yellow)"/>
      <polygon class="band-grey" points="283,204 610,204 610,279 315,279" fill="var(--brand-grey)" stroke="var(--card-white)" stroke-width="6"/>

      <g class="contact" fill="var(--ink-white)" font-size="13.5">
        <text x="41" y="212">Level 3, 218 Wexley Street</text>
        <text x="41" y="229">Melbourne 3000</text>
      </g>

      <g class="icons" fill="none" stroke="var(--ink-white)" stroke-width="1.2">
        <path d="M43 249 q0 7 7 7 l1.5-2 -2-2 -1.5 1 q-2-1-3-3 l1-1.5 -2-2 z" fill="var(--ink-white)" stroke="none"/>
        <rect x="42.5" y="266" width="9" height="6.5"/>
        <path d="M42.5 266 l4.5 3.5 4.5-3.5"/>
        <circle cx="47" cy="288" r="4.3"/>
        <path d="M42.7 288 h8.6 M47 283.7 q-3 4.3 0 8.6 M47 283.7 q3 4.3 0 8.6"/>
      </g>

      <g class="contact" fill="var(--ink-white)" font-size="13">
        <text x="61" y="257">0468 927 341</text>
        <text x="61" y="274">brennan@larkstone-partners.com.au</text>
        <text x="61" y="292">www.larkstone-partners.com.au</text>
      </g>

      <text class="person-name" x="558" y="242" text-anchor="end" font-size="18" fill="var(--ink-white)">BRENNAN ULFSSON</text>
      <text class="person-title" x="558" y="259" text-anchor="end" font-size="13.5" fill="var(--ink-white)">Consultant</text>
    </svg>
  </section>

</main>
</body>
</html>
```